I need an Oakline Office selling website

My Oakline Office store is driven by creativity and innovation. With this i am searching for an industry standard website for my Oakline Office and items selling website. I sell a wide range of Oakline Office items such as chairs, tables, burglary, cotton, wardrobe, etc. There will be a category for each of the items i sell. My business is based in the United States and services only US based residents. I don't accept online payments and customers are to pay on delivery of items. The website is to have images of the items i sell. I would like brown, black and golden colors because those are the colors furniture mostly make use of. Designs submitted should be unique.

Industry/Entity Type

Furniture Store

Coding

Coded - Design and coding required

```html
<!DOCTYPE html>
<html lang="en">
<head>
<meta charset="utf-8">
<title>Oakline Office</title>
<link href="https://fonts.googleapis.com/css2?family=Open+Sans:wght@300;400;600;700&family=Oswald:wght@300&family=Libre+Baskerville&display=swap" rel="stylesheet">
<style>
  :root {
    --gold: #fcc633;
    --black: #000000;
    --ink: #222222;
    --text: #555555;
    --white: #ffffff;
    --band: #e9e9e9;
    --footer: #232323;
    --footer-base: #111111;
    --footer-text: #bdbdbd;
  }
  * { margin: 0; padding: 0; box-sizing: border-box; }
  html, body { width: 1200px; height: 2378px; overflow: hidden; }
  body { position: relative; background: var(--white); font-family: "Open Sans", Arial, sans-serif; color: var(--ink); }
  .abs { position: absolute; }

  /* Header */
  .top-rule { left: 0; top: 0; width: 1200px; height: 6px; background: var(--black); }
  .brand { left: 79px; top: 52px; font-family: "Oswald", "Arial Narrow", sans-serif; font-weight: 300; font-size: 50px; letter-spacing: 1px; color: var(--black); line-height: 1; }
  .top-email { left: 670px; top: 16px; font-size: 17px; color: var(--ink); display: flex; align-items: center; gap: 9px; }
  .top-phone { left: 905px; top: 5px; width: 217px; height: 47px; background: var(--black); border-radius: 0 0 8px 8px; color: var(--gold); font-weight: 700; font-size: 23px; display: flex; align-items: center; justify-content: center; gap: 9px; }
  .main-nav { left: 442px; top: 60px; height: 51px; display: flex; align-items: center; font-size: 19px; color: #444; }
  .main-nav a { color: inherit; text-decoration: none; text-transform: uppercase; }
  .main-nav .nav-home { background: var(--gold); color: var(--black); width: 100px; height: 51px; display: flex; align-items: center; justify-content: center; }
  .nav-about { position: absolute; left: 124px; }
  .nav-products { position: absolute; left: 228px; }
  .nav-specials { position: absolute; left: 371px; }
  .nav-news { position: absolute; left: 498px; }
  .nav-contact { position: absolute; left: 596px; }

  /* Hero */
  .hero { left: 0; top: 146px; width: 1200px; height: 572px; background: linear-gradient(90deg, #e6e9ea 0%, #f4f5f5 30%, #b9c6cb 55%, #8ea1a7 100%); }
  .tagline-band { left: 0; top: 718px; width: 1200px; height: 125px; background: var(--black); }
  .tagline { left: 81px; top: 752px; font-family: "Libre Baskerville", Georgia, serif; font-size: 43px; color: var(--white); }
  .btn-contact { left: 918px; top: 753px; width: 204px; height: 55px; background: var(--gold); color: var(--black); font-weight: 700; font-size: 24px; display: flex; align-items: center; justify-content: center; }

  /* Sections */
  .section-title { left: 0; width: 1200px; text-align: center; font-weight: 300; font-size: 41px; color: var(--black); text-transform: uppercase; }
  .intro { left: 172px; top: 952px; width: 856px; text-align: center; font-size: 15.5px; line-height: 25px; color: var(--text); }
  .pill { height: 51px; border-radius: 26px; background: var(--gold); color: var(--black); font-size: 20px; display: flex; align-items: center; justify-content: center; text-transform: uppercase; }
  .product { width: 244px; height: 187px; border: 1px solid #cfcfcf; }

  /* Testimonials */
  .testimonials { left: 0; top: 1775px; width: 1200px; height: 289px; background: var(--band); }
  .client-photo { left: 125px; top: 1881px; width: 124px; height: 124px; border-radius: 50%; background: linear-gradient(180deg, #d8d4cf, #8e8a87); border: 2px solid #cccccc; }
  .quote { left: 268px; top: 1896px; width: 780px; font-size: 15.5px; line-height: 25px; color: var(--text); }
  .client-name { left: 268px; top: 1977px; font-size: 15px; font-weight: 700; color: var(--black); }

  /* Footer */
  .footer { left: 0; top: 2064px; width: 1200px; height: 260px; background: var(--footer); }
  .footer-head { top: 2090px; font-size: 24px; font-weight: 300; color: var(--white); }
  .footer-links { left: 79px; top: 2132px; list-style: none; font-size: 16px; line-height: 27px; color: var(--footer-text); }
  .footer-links li:first-child { color: var(--white); }
  .news-copy { left: 350px; top: 2132px; width: 240px; font-size: 16px; line-height: 25px; color: var(--footer-text); }
  .news-input { left: 349px; top: 2192px; width: 233px; height: 35px; border: 1px solid #888; font-size: 15px; color: var(--footer-text); padding-left: 6px; display: flex; align-items: center; }
  .news-btn { left: 349px; top: 2238px; width: 150px; height: 43px; background: var(--white); color: var(--black); font-size: 20px; display: flex; align-items: center; justify-content: center; }
  .contact-line { left: 620px; display: flex; gap: 12px; font-size: 16px; line-height: 25px; color: var(--footer-text); }
  .contact-line svg { flex: none; margin-top: 4px; }
  .social { width: 52px; height: 52px; border-radius: 50%; border: 2px solid #9a9a9a; top: 2134px; }
  .social.active { background: #cfcfcf; border-color: #cfcfcf; }
  .footer-base { left: 0; top: 2324px; width: 1200px; height: 54px; background: var(--footer-base); color: var(--footer-text); font-size: 15px; display: flex; align-items: center; justify-content: center; }
  .footer-base strong { color: var(--white); margin: 0 5px; }
</style>
</head>
<body>
  <header>
    <div class="abs top-rule"></div>
    <div class="abs brand">OAKLINE OFFICE</div>
    <div class="abs top-email">
      <svg width="20" height="15" viewBox="0 0 20 15"><rect x="1" y="1" width="18" height="13" fill="none" stroke="#222" stroke-width="1.6"/><path d="M1 1 L10 8 L19 1" fill="none" stroke="#222" stroke-width="1.6"/></svg>
      info@oaklineoffice.com
    </div>
    <div class="abs top-phone">
      <svg width="22" height="22" viewBox="0 0 24 24"><path fill="#fcc633" d="M6.6 10.8c1.4 2.8 3.8 5.1 6.6 6.6l2.2-2.2c.3-.3.7-.4 1-.2 1.1.4 2.3.6 3.6.6.6 0 1 .4 1 1V20c0 .6-.4 1-1 1C10.6 21 3 13.4 3 4c0-.6.4-1 1-1h3.5c.6 0 1 .4 1 1 0 1.3.2 2.5.6 3.6.1.3 0 .7-.2 1z"/></svg>
      123 456 7890
    </div>
    <nav class="abs main-nav">
      <a class="nav-home" href="#">Home</a>
      <a class="nav-about" href="#">About</a>
      <a class="nav-products" href="#">Products</a>
      <a class="nav-specials" href="#">Specials</a>
      <a class="nav-news" href="#">News</a>
      <a class="nav-contact" href="#">Contact</a>
    </nav>
  </header>

  <section>
    <div class="abs hero" role="img" aria-label="Bright modern office with a white sculpted wall, a yellow lounge chair and glass-walled workstations"></div>
    <div class="abs tagline-band"></div>
    <div class="abs tagline">Quality Services At Affordable Prices</div>
    <div class="abs btn-contact">CONTACT US</div>
  </section>

  <section>
    <h1 class="abs section-title" style="top:889px;">Welcome to Oakline Office</h1>
    <p class="abs intro">Lorem Ipsum is simply dummy text of the printing and typesetting industry. Lorem Ipsum has been the industry's standard dummy text ever since the 1500s, when an unknown printer took a galley of type and scrambled it to make a type specimen book.</p>
    <div class="abs pill" style="left:512px; top:1046px; width:173px;">Read More</div>
  </section>

  <section>
    <h2 class="abs section-title" style="top:1151px;">Our Products</h2>
    <div class="abs product" style="left:81px; top:1228px; background:#ffffff;" role="img" aria-label="Black mesh office chair"></div>
    <div class="abs product" style="left:346px; top:1228px; background:linear-gradient(135deg,#d23a2e,#7a3fa0 50%,#e8c640);" role="img" aria-label="Fanned colourful fabric swatches"></div>
    <div class="abs product" style="left:612px; top:1228px; background:linear-gradient(180deg,#ebebeb,#d9d9d9);" role="img" aria-label="White sofa and shelving unit"></div>
    <div class="abs product" style="left:876px; top:1228px; background:linear-gradient(180deg,#f2f2f2,#cfcfcf);" role="img" aria-label="Home office with black desk and arc lamp"></div>
    <div class="abs product" style="left:81px; top:1438px; background:linear-gradient(180deg,#dfe8ee,#9eaab2);" role="img" aria-label="Conference room with round table and black chairs"></div>
    <div class="abs product" style="left:346px; top:1438px; background:linear-gradient(180deg,#f4f4f4,#dcdcdc);" role="img" aria-label="White desk with laptop and plant"></div>
    <div class="abs product" style="left:612px; top:1438px; background:linear-gradient(180deg,#d8d8d6,#bdbdbb);" role="img" aria-label="Red swivel armchair against concrete wall"></div>
    <div class="abs product" style="left:876px; top:1438px; background:linear-gradient(180deg,#c9c3bd,#4a3b34);" role="img" aria-label="Cream sofa on dark wood floor"></div>
    <div class="abs pill" style="left:512px; top:1656px; width:176px;">View All</div>
  </section>

  <section>
    <div class="abs testimonials"></div>
    <h2 class="abs section-title" style="top:1812px;">What Our Client Say</h2>
    <svg class="abs" style="left:72px; top:1920px;" width="20" height="46" viewBox="0 0 20 46"><path d="M17 2 L4 23 L17 44" fill="none" stroke="#111" stroke-width="2"/></svg>
    <svg class="abs" style="left:1073px; top:1920px;" width="20" height="46" viewBox="0 0 20 46"><path d="M3 2 L16 23 L3 44" fill="none" stroke="#111" stroke-width="2"/></svg>
    <div class="abs client-photo" role="img" aria-label="Client portrait"></div>
    <p class="abs quote">Lorem Ipsum is simply dummy text of the printing and typesetting industry. Lorem Ipsum has been the industry's standard dummy text ever since the 1500s, when an unknown printer took a galley of type and scrambled it to make a type specimen book.</p>
    <div class="abs client-name">- CLIENT NAME</div>
  </section>

  <footer>
    <div class="abs footer"></div>
    <h3 class="abs footer-head" style="left:79px;">Useful Links</h3>
    <ul class="abs footer-links">
      <li>Home</li><li>About</li><li>Products</li><li>Specials</li><li>News</li><li>Contact</li>
    </ul>

    <h3 class="abs footer-head" style="left:350px;">Newsletter</h3>
    <p class="abs news-copy">Subscribe to stay on Oakline Office</p>
    <div class="abs news-input">Enter Email Id</div>
    <div class="abs news-btn">SUBSCRIBE</div>

    <h3 class="abs footer-head" style="left:620px;">Get In Touch</h3>
    <div class="abs contact-line" style="top:2132px; width:250px;">
      <svg width="14" height="19" viewBox="0 0 14 19"><path fill="#fff" d="M7 0C3.1 0 0 3.1 0 7c0 5 7 12 7 12s7-7 7-12c0-3.9-3.1-7-7-7zm0 9.5A2.5 2.5 0 1 1 7 4.5a2.5 2.5 0 0 1 0 5z"/></svg>
      <span>Lorem Ipsum is simply dummy text of the printing</span>
    </div>
    <div class="abs contact-line" style="top:2194px; font-weight:600; color:#ddd;">
      <svg width="18" height="18" viewBox="0 0 24 24"><path fill="#fff" d="M6.6 10.8c1.4 2.8 3.8 5.1 6.6 6.6l2.2-2.2c.3-.3.7-.4 1-.2 1.1.4 2.3.6 3.6.6.6 0 1 .4 1 1V20c0 .6-.4 1-1 1C10.6 21 3 13.4 3 4c0-.6.4-1 1-1h3.5c.6 0 1 .4 1 1 0 1.3.2 2.5.6 3.6.1.3 0 .7-.2 1z"/></svg>
      <span>123 456 7890</span>
    </div>
    <div class="abs contact-line" style="top:2232px;">
      <svg width="18" height="14" viewBox="0 0 20 15"><rect x="1" y="1" width="18" height="13" fill="none" stroke="#fff" stroke-width="1.6"/><path d="M1 1 L10 8 L19 1" fill="none" stroke="#fff" stroke-width="1.6"/></svg>
      <span>info@oaklineoffice.com</span>
    </div>

    <h3 class="abs footer-head" style="left:891px;">Connect With Us</h3>
    <div class="abs social active" style="left:889px;" aria-label="Social link"></div>
    <div class="abs social" style="left:962px;" aria-label="Social link"></div>
    <div class="abs social" style="left:1034px;" aria-label="Social link"></div>

    <div class="abs footer-base">© <strong>OAKLINE OFFICE</strong> - 2016. All Rights Reserved.</div>
  </footer>
</body>
</html>
```